GlassHaven Artbook for Okanagan Region, British Columbia

Creating an art book: GlassHaven, for the Okanagan Wine Region in British Columbia, Canada. Would like smart, modern, clean and linear...cool, sexy urban, not ugly boring suburban... I need a cover that appeals to the wino in all of us! Title: GlassHaven -Marla Dovicki
Updates
Thank you all kindly for your efforts. I have added some files so that you can get a sense of my aesthetic...it's never easy trying to figure it out, is it? I will hopefully have dimensions of book soon...cheers, Marla
would anyone please design a giant wine bottle with the wine label that looks like a label but says glasshaven...just curious to see if it works as a design or not...thank you.
Target Market(s)
Designing this wine art book of quotes to wineries in Okanagan BC. Buyer is wine lover and tourist ready to spend his vacation bucks on this wonderful book!
Look and feel

```html
<!DOCTYPE html>
<html lang="en">
<head>
<meta charset="utf-8">
<title>Glasshaven — Book Cover</title>
<link rel="stylesheet" href="https://fonts.googleapis.com/css2?family=Zilla+Slab:wght@400&family=Jost:wght@300&display=swap">
<style>
  :root {
    --page-bg: #ffffff;
    --cover-bg: #e4e4e2;
    --title-red: #ec1c24;
    --motif-dark: #1a1a1a;
    --author-grey: #555555;
  }
  * { margin: 0; padding: 0; box-sizing: border-box; }
  html, body {
    width: 1200px;
    height: 1000px;
    overflow: hidden;
    background: var(--page-bg);
  }
  .stage {
    position: relative;
    width: 1200px;
    height: 1000px;
  }
  .book-cover {
    position: absolute;
    left: 364px;
    top: 156px;
    width: 471px;
    height: 652px;
    background: var(--cover-bg);
  }
  .book-title {
    position: absolute;
    left: 0;
    right: 0;
    top: 196px;
    text-align: center;
    font-family: "Zilla Slab", Georgia, serif;
    font-weight: 400;
    font-size: 44px;
    letter-spacing: 1px;
    line-height: 1;
    color: var(--title-red);
  }
  .cover-motif {
    position: absolute;
    left: 77px;
    top: 282px;
    width: 318px;
    height: 29px;
    background: var(--motif-dark);
  }
  .book-author {
    position: absolute;
    left: 0;
    right: 0;
    top: 541px;
    text-align: center;
    font-family: "Jost", "Helvetica Neue", Arial, sans-serif;
    font-weight: 300;
    font-size: 15px;
    letter-spacing: 2.6px;
    text-transform: uppercase;
    color: var(--author-grey);
  }
</style>
</head>
<body>
  <main class="stage">
    <section class="book-cover">
      <h1 class="book-title">Glasshaven</h1>
      <div class="cover-motif" role="img" aria-label="Row of three black wine bottle silhouettes lying on their sides"></div>
      <p class="book-author">Marla Dovicki</p>
    </section>
  </main>
</body>
</html>
```